Psychiatric Office Needs a Website- 1st Time Ever!

Been in practice since 2003 with no website, but finally ready to dive in. We are Maplecrest Behavioral Healthcare, a mental health outpatient practice based in Fayetteville, Georgia that sees diverse individuals and families from childhood to advanced age for a variety of conditions. We've grown by word of mouth and referral but would now like to have a digital footprint. Be the pioneer of our website and we will be sure to share. We would like to see designs that are modern, animated, fairly colorful, easy to read, and caters to all ages. Also, we would like the design to take the whole page (not be centered) and can be viewed well on phone/tablet. Please see our outline for more information. Our motto/slogan is: Maplecrest Behavioral Healthcare- A step forward in your wellness journey, so the design should try to reflect that.
Updates

Project Deadline Extended
Reason: site in progress

Target Market(s)

Children through elderly

Industry/Entity Type

Medical

Logo Text

Stepping forward in your wellness journey

Number of Pages Required

1 page

Colors

Designer to choose colors to be used in the design.

Requirements
Must have
• Animation or moving pictures.
• Color.
• Concise.
• User friendly
• Diversity in the stock photos

```html
<!DOCTYPE html>
<html lang="en">
<head>
<meta charset="utf-8">
<title>Maplecrest Behavioral Healthcare</title>
<link rel="stylesheet" href="https://fonts.googleapis.com/css2?family=Asap:wght@400;500;600&family=Arimo:wght@400;700&display=swap">
<style>
:root{
  --purple:#4b2a86;
  --purple-dark:#3a1f6c;
  --purple-light:#6a45b0;
  --ink:#333;
  --muted:#666;
  --white:#fff;
  --line:#d8d8d8;
  --dark:#2b2b2b;
}
*{margin:0;padding:0;box-sizing:border-box}
html,body{width:1200px;height:3455px;overflow:hidden}
body{position:relative;font-family:"Arimo",Arial,sans-serif;color:var(--ink);background:var(--white)}
.abs{position:absolute}
h1,h2,h3,.heading{font-family:"Asap",Arial,sans-serif;font-weight:400}

/* top bar */
.topbar{left:0;top:0;width:1200px;height:50px;background:var(--purple-dark);color:#fff;font-size:15px}
.topbar span{position:absolute;top:15px;white-space:nowrap}
.navbar{left:0;top:50px;width:1200px;height:70px;background:#fff;border-bottom:1px solid #eee}
.nav a{position:absolute;top:26px;font-size:17px;color:#555;text-decoration:none;font-family:"Asap",sans-serif;white-space:nowrap}
.nav .active{top:-6px;height:76px;width:106px;background:var(--purple);color:#fff;text-align:center;padding-top:32px}
.brand{left:70px;top:8px;width:120px;height:120px;border-radius:50%;background:var(--purple);border:5px solid #fff;box-shadow:0 0 0 2px var(--purple);color:#fff;font-family:"Asap",sans-serif;font-size:14px;text-align:center;padding-top:33px;line-height:1.3;z-index:2}

/* hero */
.hero{left:0;top:120px;width:1200px;height:571px;background:linear-gradient(180deg,#9fb48a,#c7b79e 55%,#6f8d4f)}
.hero-box{left:210px;top:283px;width:782px;height:200px;background:rgba(60,60,70,.45)}
.hero-title{left:210px;top:295px;width:782px;text-align:center;color:#fff;font-size:48px;line-height:60px;white-space:nowrap}
.hero-sub{left:210px;top:358px;width:782px;text-align:center;color:#fff;font-size:22px;line-height:28px;font-style:italic;white-space:nowrap}
.btn{background:var(--purple);color:#fff;font-family:"Asap",sans-serif;text-align:center}
.hero-btn{left:507px;top:403px;width:186px;height:56px;line-height:56px;font-size:20px}

/* vision / mission */
.vm-left{left:0;top:691px;width:600px;height:369px;background:var(--purple)}
.vm-right{left:600px;top:691px;width:600px;height:369px;background:#fff}
.vm-title{font-size:36px;font-family:"Asap",sans-serif;white-space:nowrap}
.vm-title::after{content:"";display:block;width:160px;height:2px;background:currentColor;margin-top:6px}
.vm-text{font-size:15px;line-height:25px;width:355px}
.seal{left:460px;top:725px;width:280px;height:280px;border-radius:50%;background:var(--purple);border:8px solid #fff;box-shadow:0 0 0 3px var(--purple);color:#fff;text-align:center;font-family:"Asap",sans-serif;font-size:22px;padding-top:105px;line-height:1.35}

/* services */
.services{left:0;top:1060px;width:1200px;height:833px;background:linear-gradient(135deg,#3a3a3d,#5a5a5e 50%,#2c2c2e)}
.sec-title{width:1200px;text-align:center;color:#fff;font-size:36px;font-family:"Asap",sans-serif}
.sec-title::after{content:"";display:block;width:160px;height:2px;background:#fff;margin:6px auto 0}
.ring{border-radius:50%;border:6px solid var(--purple);background:linear-gradient(135deg,#c9a98b,#8b6f66)}
.svc{color:#fff;font-size:14px;line-height:19px;width:240px}
.svc b{display:block;font-weight:400;font-size:17px;margin-bottom:4px;font-family:"Asap",sans-serif;white-space:nowrap}
.svc u{font-weight:700;white-space:nowrap}

/* conditions */
.conditions{left:0;top:1893px;width:1200px;height:553px;background:linear-gradient(135deg,#3f2175,#6b43b3)}
.card-img{width:253px;height:168px;background:linear-gradient(135deg,#b89a85,#6d5a66);box-shadow:0 4px 10px rgba(0,0,0,.4)}
.card-title{width:253px;text-align:center;color:#fff;font-size:21px;font-family:"Asap",sans-serif;line-height:24px}
.card-text{width:253px;text-align:center;color:#fff;font-size:13px;line-height:19px}
.arrow{width:30px;height:30px;background:#fff;color:var(--purple);text-align:center;line-height:28px;font-size:20px}
.dot{width:14px;height:14px;border:2px solid #fff}

/* faq / news */
.faq-title{font-size:38px;color:var(--purple);font-family:"Asap",sans-serif}
.faq-item{width:520px;border:1px solid var(--line);font-size:20px;color:var(--purple);font-family:"Asap",sans-serif;padding:10px 14px;white-space:nowrap}
.faq-item i{font-style:normal;font-weight:600;margin-right:14px}
.faq-item p{white-space:normal}
.divider{left:613px;top:2450px;width:10px;height:420px;background:#eee}
.news-img{width:116px;height:106px;background:linear-gradient(135deg,#c9b59c,#7b6b5d)}
.news-title{font-size:19px;color:var(--purple);font-family:"Asap",sans-serif;white-space:nowrap}
.news-meta{font-size:12px;color:#888}
.news-text{font-size:14px;color:#555;line-height:20px;width:330px}
.news-more{font-size:13px;color:var(--purple);font-weight:700}

/* cta */
.cta{left:0;top:2874px;width:1200px;height:108px;background:var(--purple)}
.cta-text{left:78px;width:780px;color:#fff;font-size:15px;line-height:24px}
.cta-btn{left:895px;top:2897px;width:228px;height:56px;line-height:56px;background:#fff;color:var(--purple);text-align:center;font-size:20px;font-family:"Asap",sans-serif}

/* footer */
.footer{left:0;top:2982px;width:1200px;height:399px;background:linear-gradient(135deg,#3d2a3a,#5a4048 50%,#2e2430)}
.f-title{color:#fff;font-size:20px;font-family:"Asap",sans-serif}
.field{left:80px;width:448px;height:40px;background:#fff;font-size:14px;color:#777;padding:12px 14px}
.f-list{color:#fff;font-size:15px;line-height:29px;list-style:none}
.f-list li::before{content:"";display:inline-block;width:7px;height:7px;border-radius:50%;background:#fff;margin-right:12px;vertical-align:middle}
.f-info{color:#fff;font-size:14px;line-height:20px;white-space:nowrap}
.social{width:48px;height:48px;border-radius:50%;background:var(--purple)}
.copy{left:0;top:3381px;width:1200px;height:74px;background:#2a2228;color:#fff;text-align:center;font-size:14px;line-height:74px;border-top:1px solid #555}
</style>
</head>
<body>

<div class="abs topbar">
  <span style="left:505px">&#9719; Monday - Friday : 10.00 A.M to 8.00 P.M</span>
  <span style="left:818px">&#9742; +1-555-014-2273</span>
  <span style="left:980px">LOGIN</span>
  <span style="left:1040px">&#9679; Patient</span>
</div>
<div class="abs navbar">
  <nav class="nav">
    <a class="active" style="left:357px">Home</a>
    <a style="left:505px">About Us</a>
    <a style="left:607px">Services</a>
    <a style="left:700px">Conditions We Treat</a>
    <a style="left:888px">New Patients</a>
    <a style="left:1022px">Contact Us</a>
  </nav>
</div>
<div class="abs brand">Maplecrest<br>Behavioral<br>Healthcare</div>

<section>
  <div class="abs hero" role="img" aria-label="Photo of a smiling multi-generation family outdoors"></div>
  <div class="abs hero-box"></div>
  <h1 class="abs hero-title">Maplecrest Behavioral Healthcare</h1>
  <p class="abs hero-sub">A step forward in your wellness journey</p>
  <div class="abs btn hero-btn">CONTACT US</div>
</section>

<section>
  <div class="abs vm-left"></div>
  <div class="abs vm-right"></div>
  <div class="abs vm-title" style="left:80px;top:740px;color:#fff">&#9734; VISION</div>
  <p class="abs vm-text" style="left:80px;top:808px;color:#fff">Lorem Ipsum is simply dummy text of the printing and typesetting industry. Lorem Ipsum has been the industry's standard dummy text ever since the 1500s, when an unknown printer took a galley of type and scrambled it to make a type specimen book. It has survived not only five centuries, but also the leap into electronic typesetting, remaining essentially unchanged.</p>
  <div class="abs vm-title" style="left:768px;top:740px;color:var(--purple)">&#9678; MISSION</div>
  <p class="abs vm-text" style="left:772px;top:808px;color:#666">Lorem Ipsum is simply dummy text of the printing and typesetting industry. Lorem Ipsum has been the industry's standard dummy text ever since the 1500s, when an unknown printer took a galley of type and scrambled it to make a type specimen book. It has survived not only five centuries, but also the leap into electronic typesetting, remaining essentially unchanged.</p>
  <div class="abs seal">Maplecrest<br>Behavioral Healthcare</div>
</section>

<section>
  <div class="abs services" role="img" aria-label="Blurred photo of a counselling session"></div>
  <h2 class="abs sec-title" style="left:0;top:1105px">SERVICES</h2>
  <svg class="abs" style="left:0;top:1060px" width="1200" height="833">
    <g stroke="#fff" stroke-width="2" fill="none">
      <line x1="599" y1="391" x2="500" y2="204"/>
      <line x1="599" y1="391" x2="691" y2="195"/>
      <line x1="599" y1="391" x2="396" y2="340"/>
      <line x1="599" y1="391" x2="801" y2="340"/>
      <line x1="599" y1="391" x2="444" y2="529"/>
      <line x1="599" y1="391" x2="767" y2="513"/>
      <line x1="599" y1="391" x2="608" y2="598"/>
    </g>
    <circle cx="599" cy="391" r="112" fill="none" stroke="#fff" stroke-width="2"/>
    <circle cx="599" cy="391" r="100" fill="#fff"/>
    <circle cx="599" cy="391" r="40" fill="var(--purple)"/>
  </svg>
  <div class="abs ring" style="left:438px;top:1202px;width:124px;height:124px" role="img" aria-label="Clinician with patient"></div>
  <div class="abs ring" style="left:629px;top:1193px;width:124px;height:124px" role="img" aria-label="Person reviewing paperwork"></div>
  <div class="abs ring" style="left:334px;top:1338px;width:124px;height:124px" role="img" aria-label="Counsellor talking with client"></div>
  <div class="abs ring" style="left:739px;top:1338px;width:124px;height:124px" role="img" aria-label="Child playing with blocks"></div>
  <div class="abs ring" style="left:382px;top:1527px;width:124px;height:124px" role="img" aria-label="Doctor consultation"></div>
  <div class="abs ring" style="left:705px;top:1511px;width:124px;height:124px" role="img" aria-label="Distressed person"></div>
  <div class="abs ring" style="left:546px;top:1596px;width:124px;height:124px" role="img" aria-label="Family group"></div>

  <div class="abs svc" style="left:140px;top:1212px;width:220px;padding-left:0"><b>Diagnostic evaluation and treatment</b>Lorem Ipsum is simply dummy text of the printing and text typesetting industry.<u>READ MORE</u></div>
  <div class="abs svc" style="left:770px;top:1199px;width:240px"><b>Disability and work-related reports</b>Lorem Ipsum is simply dummy text of the printing and text typesetting industry.<u>READ MORE</u></div>
  <div class="abs svc" style="left:80px;top:1382px;width:230px"><b>Psychopharmacology</b>Lorem Ipsum is simply dummy text of the printing and text typesetting industry.<u>READ MORE</u></div>
  <div class="abs svc" style="left:887px;top:1357px;width:250px"><b>Early childhood Assessments</b>Lorem Ipsum is simply dummy text of the printing and text typesetting industry.<u>READ MORE</u></div>
  <div class="abs svc" style="left:100px;top:1573px;width:250px"><b>Bariatric pre-surgical consultation</b>Lorem Ipsum is simply dummy text of the printing and text typesetting industry.<u>READ MORE</u></div>
  <div class="abs svc" style="left:862px;top:1545px;width:250px"><b>Substance abuse assessments</b>Lorem Ipsum is simply dummy text of the printing and text typesetting industry.<u>READ MORE</u></div>
  <div class="abs svc" style="left:500px;top:1748px;width:220px"><b>Developmental disabilities</b>Lorem Ipsum is simply dummy text of the printing and text typesetting industry.<u>READ MORE</u></div>
</section>

<section>
  <div class="abs conditions"></div>
  <h2 class="abs sec-title" style="left:0;top:1952px">CONDITIOND WE TREAT</h2>
  <div class="abs arrow" style="left:32px;top:2108px">&#8249;</div>
  <div class="abs arrow" style="left:1138px;top:2108px">&#8250;</div>

  <div class="abs card-img" style="left:78px;top:2043px" role="img" aria-label="Woman holding her head in distress"></div>
  <div class="abs card-title" style="left:78px;top:2229px">Mood Disorders</div>
  <p class="abs card-text" style="left:78px;top:2276px">Lorem Ipsum is simply dummy text of the printing and typesetting industry. Lorem Ipsum has been the industry's standard dummy text ever since.</p>

  <div class="abs card-img" style="left:343px;top:2043px" role="img" aria-label="Counsellor comforting a client"></div>
  <div class="abs card-title" style="left:343px;top:2229px">Anxiety Disorders</div>
  <p class="abs card-text" style="left:343px;top:2276px">Lorem Ipsum is simply dummy text of the printing and typesetting industry. Lorem Ipsum has been the industry's standard dummy text ever since.</p>

  <div class="abs card-img" style="left:608px;top:2043px" role="img" aria-label="Therapist session with patient"></div>
  <div class="abs card-title" style="left:608px;top:2229px">Psychotic Disorders</div>
  <p class="abs card-text" style="left:608px;top:2276px">Lorem Ipsum is simply dummy text of the printing and typesetting industry. Lorem Ipsum has been the industry's standard dummy text ever since.</p>

  <div class="abs card-img" style="left:873px;top:2043px" role="img" aria-label="Mother hugging her child"></div>
  <div class="abs card-title" style="left:873px;top:2217px">Common Disorders<br>of Childhood</div>
  <p class="abs card-text" style="left:873px;top:2276px">Lorem Ipsum is simply dummy text of the printing and typesetting industry. Lorem Ipsum has been the industry's standard dummy text ever since.</p>

  <div class="abs dot" style="left:573px;top:2409px"></div>
  <div class="abs dot" style="left:591px;top:2409px;background:#fff"></div>
  <div class="abs dot" style="left:609px;top:2409px"></div>
</section>

<section>
  <h2 class="abs faq-title" style="left:80px;top:2490px">FAQ</h2>
  <div class="abs faq-item" style="left:80px;top:2555px;height:131px"><i>&#8211;</i>What do I need to bring with me to my first visit?
    <p style="font-family:Arimo,sans-serif;font-size:12px;color:#555;line-height:19px;margin-top:10px;padding-top:8px;border-top:1px solid var(--line)">Lorem Ipsum is simply dummy text of the printing and typesetting industry. Lorem Ipsum has been the industry's standard dummy text ever since the 1500s, it has survived not only five centuries, but also the leap into electronic typesetting, remaining essentially unchanged.</p></div>
  <div class="abs faq-item" style="left:80px;top:2690px"><i>+</i>How long do I have to wait to be seen?</div>
  <div class="abs faq-item" style="left:80px;top:2734px"><i>+</i>Why is my child not doing well in school?</div>
  <div class="abs faq-item" style="left:80px;top:2778px"><i>+</i>What typs of insurance do you accept?</div>

  <div class="abs divider"></div>

  <h2 class="abs faq-title" style="left:668px;top:2490px">LATEST NEWS</h2>
  <div class="abs news-img" style="left:668px;top:2552px" role="img" aria-label="Child studying"></div>
  <div class="abs news-title" style="left:797px;top:2552px">Lorem Ipsum is simply dummy text</div>
  <div class="abs news-meta" style="left:797px;top:2582px">&#9635; 10 JULY 2016</div>
  <p class="abs news-text" style="left:797px;top:2602px">Lorem Ipsum is simply dummy text of the printing and typesetting industry.......</p>
  <div class="abs news-more" style="left:797px;top:2652px">READ MORE &nbsp; &raquo;</div>
  <div class="abs" style="left:668px;top:2683px;width:400px;height:1px;background:var(--line)"></div>
  <div class="abs news-img" style="left:668px;top:2712px" role="img" aria-label="Family reading together"></div>
  <div class="abs news-title" style="left:797px;top:2712px">Lorem Ipsum is simply dummy text</div>
  <div class="abs news-meta" style="left:797px;top:2742px">&#9635; 10 JULY 2016</div>
  <p class="abs news-text" style="left:797px;top:2762px">Lorem Ipsum is simply dummy text of the printing and typesetting industry.......</p>
  <div class="abs news-more" style="left:797px;top:2812px">READ MORE &nbsp; &raquo;</div>
</section>

<section>
  <div class="abs cta"></div>
  <p class="abs cta-text" style="top:2903px">Lorem Ipsum is simply dummy text of the printing and typesetting industry. Lorem Ipsum has been the industry's standard dummy text ever since the 1500s, when an unknown printer took a galley of type and scrambled.</p>
  <div class="abs cta-btn">NEW PATIENT FORM</div>
</section>

<footer>
  <div class="abs footer" role="img" aria-label="Faded photo of a family gathering"></div>
  <h3 class="abs f-title" style="left:80px;top:3035px">QUICK INQUIRY</h3>
  <div class="abs field" style="top:3083px">Name*</div>
  <div class="abs field" style="top:3130px">Email*</div>
  <div class="abs field" style="top:3177px">Services*</div>
  <div class="abs field" style="top:3224px;height:94px">Message*</div>
  <div class="abs btn" style="left:80px;top:3327px;width:186px;height:50px;line-height:50px;font-size:20px">SUBMIT</div>

  <h3 class="abs f-title" style="left:569px;top:3035px">OUR SERVICES</h3>
  <ul class="abs f-list" style="left:591px;top:3073px">
    <li>Home</li><li>About Us</li><li>Services</li><li>Conditions We Treat</li><li>New Patients</li><li>Contact Us</li>
  </ul>

  <h3 class="abs f-title" style="left:873px;top:3035px">FIND US</h3>
  <svg class="abs" style="left:873px;top:3083px" width="26" height="210" fill="#fff">
    <path d="M11 0a9 9 0 0 1 9 9c0 7-9 17-9 17S2 16 2 9a9 9 0 0 1 9-9zm0 5a4 4 0 1 0 0 8 4 4 0 0 0 0-8z"/>
    <path d="M4 90h6l3 6-3 3c2 4 5 7 9 9l3-3 6 3v6c-13 0-24-11-24-24z"/>
    <rect x="3" y="135" width="18" height="16" rx="2"/>
    <path d="M2 180h20v14H2zm1 1 9 7 9-7" fill="none" stroke="#fff" stroke-width="2"/>
  </svg>
  <p class="abs f-info" style="left:910px;top:3083px">Maplecrest Behavioral Healthcare<br>Lorem Ipsum is simply dummy<br>text printing and typesetting</p>
  <p class="abs f-info" style="left:910px;top:3175px">+1-555-014-2273</p>
  <p class="abs f-info" style="left:910px;top:3220px">+1-555-014-2273</p>
  <p class="abs f-info" style="left:910px;top:3265px">info@maplecrestcare.example</p>
  <div class="abs social" style="left:873px;top:3306px"></div>
  <div class="abs social" style="left:930px;top:3306px"></div>
  <div class="abs social" style="left:987px;top:3306px"></div>

  <div class="abs copy">&copy; MAPLECREST BEHAVIORAL HEALTHCARE- 2017. All Rights Reserved</div>
</footer>

</body>
</html>
```